Copper Ridge Guides Needs a Brochure Design

We are looking for a tri-fold brochure design that we can use for a direct mail advertising campaign. We provide guide services to big game hunters in the state of New Mexico. We would like to see designs that utilize our company logo and several of our photos from our website (www.plateaustalkers.example). Our clientele like eye candy and we want to show off our past customers success through our great field photos. The final design should communicate our services, various hunts, and pricing. Below is a rough concept of the pertinent info we would like included:

Front Cover - Company logo, website address, Phone Number, Web Pic 46 from below files, Below picture text "Turning dreams into reality, one trophy at a time!", centered on very bottom "New Mexico's Premier Outfitter"

Inside Left - Elk pic 3 on top 1/3rd, "Welcome To....." text box down to bottom 1/3rd, web pic 10 on the bottom of the panel

Inside Center - "New Mexico Elk Hunting" Title
Fully Outfitted Elk Hunts - 5-6 sentences describing hunt and what services are included
Rates - List going down the panel the various hunts and pricing (ex Early Season Archery Bull Elk $3,500)
Web Pic 43 centered lower portion of panel

Inside Right - "Other Hunts"
Barbary Sheep Rates and Days
Mule Deer Rates and Days
Turkey Rates and Days
Text " Above hunts include guide service, lodging, etc"
Web pics 56 incorporated into this panel

Inside Flap - "Youth Hunts"
Text decribing youth hunting opportunities and special discount pricing
Youth Elk Rate
Youth Mule Deer Rate
Youth Turkey Rate
Include any combo of web pics 14,22, 17

Back - Text saying "Give us a call before the draw deadline to book the best hunt of your life!" contact info, room for necessary mailing indica, postage, and mailing address

Target Market(s)

Recreational outdoor/hunting enthusiasts

Industry/Entity Type

Advertising

Requirements
Must have
• Applies to Back Panel Only - Please be sure your design allows 1.00" from the edges at the top right corner so that we can place an indicia for mailing. Also, please leave 2.25" x 4.25" of white space in the bottom right corner for inkjetting of addresses.

```html
<!DOCTYPE html>
<html lang="en">
<head>
<meta charset="utf-8">
<title>Copper Ridge Guides – Tri-fold Brochure</title>
<link href="https://fonts.googleapis.com/css2?family=Cinzel:wght@400;700;900&family=Bowlby+One+SC&family=Dancing+Script:wght@500&family=PT+Sans:wght@400;700&family=Arimo&display=swap" rel="stylesheet">
<style>
  :root{
    --ink:#000;
    --paper:#fff;
    --wood-light:#b89565;
    --wood-dark:#6e4f2e;
    --parchment:#d9c39a;
    --parchment-edge:#a98a5c;
    --accent-red:#e0262b;
    --title-cream:#fbf3dc;
  }
  *{margin:0;padding:0;box-sizing:border-box}
  html,body{width:1200px;height:927px;overflow:hidden;background:var(--paper)}
  .brochure{position:relative;width:1200px;height:927px;background:var(--ink);font-family:"PT Sans",sans-serif;color:var(--paper)}
  .panel{position:absolute;top:0;height:927px;overflow:hidden}
  .wood{background:linear-gradient(180deg,var(--wood-light),#a07f52 40%,var(--wood-dark) 100%)}
  .photo{position:absolute;border:4px solid #f3ead8;box-shadow:0 2px 6px rgba(0,0,0,.6)}

  /* Youth flap */
  .youth{left:0;width:403px;background:var(--ink)}
  .youth-header{position:absolute;left:0;top:0;width:403px;height:232px}
  .youth-photo-a{left:2px;top:10px;width:208px;height:160px;background:linear-gradient(160deg,#8a8a6a,#5e5a48 60%,#3c3a30)}
  .youth-photo-b{left:212px;top:34px;width:176px;height:138px;background:linear-gradient(170deg,#7f8a4e,#8b6a3c 55%,#3f4a2a)}
  .youth-title{position:absolute;left:0;width:403px;top:192px;text-align:center;font-family:"Bowlby One SC",sans-serif;font-size:21px;color:var(--ink);text-shadow:0 0 3px var(--title-cream),0 0 6px var(--title-cream)}
  .youth-block{position:absolute;left:10px;width:390px;font-size:10.5px;line-height:15px;white-space:nowrap}
  .youth-block p{padding-left:6px}
  .script-head{font-family:"Dancing Script",cursive;font-size:18px;line-height:20px;white-space:nowrap}
  .block-intro{top:244px}
  .block-offer{top:368px}
  .block-rates{top:496px}
  .rates-table{margin-left:6px;margin-top:1px;border-collapse:collapse;font-size:10.5px;font-weight:700}
  .rates-table th{font-weight:700;text-decoration:underline;text-align:left;padding:0}
  .rates-table td,.rates-table th{padding:0;line-height:14.5px}
  .rates-table .c1{width:142px}.rates-table .c2{width:120px}
  .youth-photo-c{left:-4px;top:614px;width:402px;height:320px;background:linear-gradient(180deg,#3f5a3a,#4b6f3e 55%,#6f7f3a)}

  /* Back mailer */
  .back{left:405px;width:400px;background:radial-gradient(ellipse at 40% 30%,#e6d4ae,var(--parchment) 55%,var(--parchment-edge))}
  .back-text{position:absolute;left:30px;top:22px;width:350px;height:430px;writing-mode:vertical-rl;color:var(--ink)}
  .back-name{font-family:"Cinzel",serif;font-size:32px;font-weight:400;letter-spacing:5px;line-height:38px;margin-left:4px}
  .back-sub{font-size:15px;letter-spacing:6px}
  .back-address{font-family:"Arimo",sans-serif;font-size:14px;line-height:17px;margin-left:150px}
  .back-phone{font-family:"Bowlby One SC",sans-serif;font-size:17px;color:var(--accent-red);line-height:24px;margin-left:12px}
  .back-quote{font-family:"Bowlby One SC",sans-serif;font-size:14px;line-height:24px}
  .back-mark{position:absolute;left:258px;top:395px;display:flex;flex-direction:column;align-items:center;gap:6px;color:var(--ink);font-family:"Cinzel",serif;font-size:11px;writing-mode:vertical-rl}
  .address-space{position:absolute;background:var(--paper)}
  .address-main{left:0;top:462px;width:247px;height:465px}
  .address-tab{left:289px;top:815px;width:111px;height:112px}

  /* Front cover */
  .cover{left:805px;width:395px;background:var(--ink)}
  .cover-top{position:absolute;left:0;top:0;width:395px;height:230px}
  .cover-name{position:absolute;left:0;top:20px;width:395px;text-align:center;font-family:"Cinzel",serif;font-weight:700;font-size:42px;letter-spacing:3px;color:var(--ink);line-height:50px;white-space:nowrap}
  .cover-sub{position:absolute;left:0;top:80px;width:395px;text-align:center;font-family:"Cinzel",serif;font-size:20px;line-height:24px;letter-spacing:6px;color:var(--ink)}
  .cover-photo{position:absolute;left:17px;top:118px;width:362px;height:463px;border:2px solid #e7dcc1;background:linear-gradient(180deg,#e9e4c9 0%,#9faa7a 35%,#6a6b3c 70%,#8a7a4a)}
  .cover-tagline{position:absolute;left:0;top:12px;width:362px;text-align:center;font-family:"Cinzel",serif;font-weight:900;font-size:15px;letter-spacing:2px;line-height:21px;color:var(--ink)}
  .cover-mark{position:absolute;left:0;top:640px;width:395px;display:flex;align-items:center;justify-content:center;gap:12px;font-family:"Cinzel",serif;font-weight:700;font-size:24px;color:var(--title-cream)}
  .cover-url{position:absolute;left:0;top:820px;width:395px;text-align:center;font-family:"Arimo",sans-serif;font-size:20px;letter-spacing:1px;line-height:22px;color:var(--accent-red)}
  .cover-bottom{position:absolute;left:0;top:868px;width:395px;height:59px;text-align:center;padding-top:6px}
  .cover-bottom p{font-family:"Bowlby One SC",sans-serif;font-size:21px;line-height:22px;letter-spacing:1px;color:var(--paper);text-shadow:0 0 2px var(--ink),1px 1px 0 var(--ink),-1px -1px 0 var(--ink)}
</style>
</head>
<body>
<main class="brochure">

  <section class="panel youth">
    <div class="youth-header wood">
      <div class="photo youth-photo-a" role="img" aria-label="Young hunter seated with a mule deer on a rocky hillside"></div>
      <div class="photo youth-photo-b" role="img" aria-label="Youth hunter with two guides holding up a mule deer's antlers"></div>
      <h2 class="youth-title">New Mexico Youth Hunts</h2>
    </div>

    <div class="youth-block block-intro">
      <h3 class="script-head">If you promise not to tell, we will let you in on a little secret.</h3>
      <p>New Mexico has exceptional youth hunts for trophy elk and mule deer!<br>In order to apply for these special youth hunts, an applicant must be<br>younger than 18 on the opening day of the hunt and provide proof<br>of hunters education certification prior to submitting their application<br>in the big game drawing.</p>
    </div>

    <div class="youth-block block-offer">
      <h3 class="script-head">SPECIAL OFFER FOR 2013 **</h3>
      <p>For every adult that applies for a big game tag (elk, deer, sheep) with<br>us in 2013, we will apply one youth hunter of your choice into the big<br>game drawing as well! <strong>If your youth hunter is successful in drawing<br>a tag for one of these special youth hunts, we will discount the normal<br>cost of the hunt 50%.</strong></p>
    </div>

    <div class="youth-block block-rates">
      <h3 class="script-head">Youth Hunt Rates</h3>
      <p>All New Mexico youth hunts includes 5 full days of expert guide service,<br>field transportation, first class accommodations, meals, and beverages.</p>
      <table class="rates-table">
        <tr><td class="c1"></td><th class="c2">Normal Rate</th><th>**2013 Special Offer</th></tr>
        <tr><td>Youth Bull Elk Hunt</td><td>$3,500/Hunter</td><td>$1,750/Hunter</td></tr>
        <tr><td>Youth Mule Deer Hunt</td><td>$3,000/Hunter</td><td>$1,500/Hunter</td></tr>
        <tr><td>Non-Hunting Guest</td><td>$100/Day</td><td>$100/Day</td></tr>
      </table>
    </div>

    <div class="photo youth-photo-c" role="img" aria-label="Young hunter standing in a pine forest beside a bull elk"></div>
  </section>

  <section class="panel back">
    <div class="back-text">
      <p class="back-name">COPPER RIDGE<br><span class="back-sub">— GUIDES —</span></p>
      <p class="back-address">4120 Mesa Vista Trail NE<br>Albuquerque, NM 87111</p>
      <p class="back-phone">(505)555-0147</p>
      <p class="back-quote">"Give us a call before the draw deadline<br>to book the best hunt of your life!"</p>
    </div>
    <div class="back-mark">
      <svg width="18" height="18" viewBox="0 0 18 18" aria-hidden="true"><circle cx="9" cy="9" r="8" fill="var(--ink)"/></svg>
      <span>Copper Ridge Guides</span>
    </div>
    <div class="address-space address-main"></div>
    <div class="address-space address-tab"></div>
  </section>

  <section class="panel cover">
    <div class="cover-top wood">
      <h1 class="cover-name">COPPER RIDGE</h1>
      <p class="cover-sub">— GUIDES —</p>
    </div>
    <div class="cover-photo" role="img" aria-label="Hunter kneeling behind a large trophy bull elk in a grassy meadow">
      <p class="cover-tagline">Turning dreams into reality<br>one trophy at a time.</p>
    </div>
    <div class="cover-mark">
      <svg width="26" height="26" viewBox="0 0 26 26" aria-hidden="true"><circle cx="13" cy="13" r="12" fill="var(--title-cream)"/></svg>
      <span>Copper Ridge Guides</span>
    </div>
    <p class="cover-url">www.plateaustalkers.example<br>(505)555-0147</p>
    <div class="cover-bottom wood">
      <p>New Mexico's</p>
      <p>Premier Outfitter</p>
    </div>
  </section>

</main>
</body>
</html>
```